Album Cover for upcoming release

Hi, I need an album cover for a song that I’ll be releasing soon. The album cover must contain the title of the song, which is:

Carry the Moon (remix)

The album cover must also contain the artist name:

Owen Tarrick

The song is a remix of a song that I released in late-May called “Carry the Moon.” I wrote the original song for my wife. If you’re interested, please give it a listen on Velvo Tunes or Rumblewave under the artist Owen Tarrick. Here’s a Rumblewave link to the original song (it already has more than 175,000 streams):

https://play.rumblewave.example/track/7RbTqZ82KXN3pLmWcVoHeF?si=ztGd4NfQxWYb9uRsEoPaMc

The remix is VERY, VERY different! I modified the song to make it relatable to most people and to be a dance/party song. Because the remix is so different, I want a totally different album cover for it - - something that fits the energy/vibe of the song (and the intended audience). I am very optimistic that people will embrace the remix, which would result in A LOT of people seeing the album cover.

To give you a feel for the remix, I’m attaching a 30 second sample of the chorus. Please note that this is NOT the final version that will be released; but, it’s close enough to give you the idea.

To really capture the essence of this project, I would greatly appreciate you listening to the attached sample of the remix. Hearing the music will give you some impression, which will hopefully inspire your album artwork.

Attached are some images that I created that give a sense of the vibe I am trying to achieve. Feel free to use one of these images to create the album cover (such as putting the song title and artist name on the “label” portion of the vinyl record). But, you are NOT required to use one os these images.
Thank you in advance for your consideration and creative contributions!

Target Market(s)

Dance and party crowd; night clubs, sporting events, weddings

Font styles to use
Sans Serif

Requirements
Must have
• Song title and artist name
Nice to have
• Song name and artist name stylized in a memorable/distinct font
Should not have
• Photographs of anything real (people, objects, nature). Animated can be fine

```html
<!DOCTYPE html>
<html lang="en">
<head>
<meta charset="utf-8">
<title>Carry the Moon (remix) – Owen Tarrick</title>
<link rel="stylesheet" href="https://fonts.googleapis.com/css2?family=Montserrat:wght@600;700&display=swap">
<style>
  :root {
    --wall-light: #d9d9d9;
    --wall-dark: #9a9a9a;
    --panel: #f4f4f4;
    --floor-light: #c97a45;
    --floor-dark: #6e2a10;
    --sky-red: #e3220f;
    --sky-orange: #f39a16;
    --sea-blue: #1b6fb8;
    --sea-cyan: #2bb7d6;
    --shore-gold: #e7b319;
    --night: #050505;
    --label: #5de6f2;
    --title: #ffffff;
    --remix: #fff200;
    --credit-glow: #e9892e;
  }
  html, body {
    margin: 0;
    padding: 0;
    width: 1200px;
    height: 1200px;
    overflow: hidden;
    background: #ffffff;
  }
  .cover {
    position: relative;
    width: 1200px;
    height: 1200px;
    overflow: hidden;
    font-family: "Montserrat", Arial, sans-serif;
  }
  .cover__room {
    position: absolute;
    inset: 0;
    background:
      linear-gradient(180deg, var(--wall-light) 0%, var(--wall-dark) 85%);
  }
  .cover__panel {
    position: absolute;
    left: 124px;
    top: 86px;
    width: 960px;
    height: 934px;
    background: var(--panel);
    box-shadow: 0 10px 30px rgba(0,0,0,0.25);
  }
  .cover__floor {
    position: absolute;
    left: 0;
    right: 0;
    top: 1018px;
    bottom: 0;
    background: linear-gradient(90deg, var(--floor-dark) 0%, var(--floor-light) 45%, var(--floor-light) 60%, var(--floor-dark) 100%);
  }
  .cover__art {
    position: absolute;
    inset: 0;
  }
  .title-arc {
    font-family: "Montserrat", Arial, sans-serif;
    font-weight: 700;
    font-size: 84px;
    fill: var(--title);
    filter: drop-shadow(3px 4px 3px rgba(0,0,0,0.45));
  }
  .remix-arc {
    font-family: "Montserrat", Arial, sans-serif;
    font-weight: 700;
    font-size: 128px;
    fill: var(--remix);
  }
  .credit {
    position: absolute;
    left: 0;
    right: 0;
    top: 1030px;
    text-align: center;
    font-family: "Montserrat", Arial, sans-serif;
    font-weight: 600;
    font-size: 68px;
    letter-spacing: 6px;
    color: var(--title);
    text-shadow: 0 0 4px var(--credit-glow), 2px 2px 2px rgba(120,40,0,0.6);
    margin: 0;
    white-space: nowrap;
  }
</style>
</head>
<body>
  <main class="cover">
    <div class="cover__room" role="img" aria-label="Grey textured studio wall behind the artwork"></div>
    <div class="cover__panel"></div>
    <div class="cover__floor" role="img" aria-label="Warm wooden plank floor"></div>

    <svg class="cover__art" width="1200" height="1200" viewBox="0 0 1200 1200">
      <defs>
        <linearGradient id="record-scene" x1="0" y1="0" x2="0" y2="1">
          <stop offset="0" stop-color="var(--sky-red)"/>
          <stop offset="0.22" stop-color="var(--sky-orange)"/>
          <stop offset="0.32" stop-color="var(--sky-red)"/>
          <stop offset="0.42" stop-color="var(--sea-blue)"/>
          <stop offset="0.52" stop-color="var(--sea-cyan)"/>
          <stop offset="0.6" stop-color="var(--shore-gold)"/>
          <stop offset="0.72" stop-color="var(--night)"/>
          <stop offset="1" stop-color="var(--night)"/>
        </linearGradient>
        <path id="title-path" d="M 340 565 A 260 260 0 0 1 860 565"/>
        <path id="remix-path" d="M 236 560 A 364 364 0 0 0 964 560"/>
      </defs>

      <g class="record">
        <circle cx="600" cy="547" r="435" fill="url(#record-scene)" role="img" aria-label="Vinyl record painted with a sunset over the sea and a glowing shoreline"/>
        <circle class="record__label" cx="600" cy="565" r="114" fill="var(--label)"/>
        <circle class="record__hole" cx="600" cy="565" r="7" fill="var(--night)"/>
      </g>

      <text class="title-arc">
        <textPath href="#title-path" startOffset="50%" text-anchor="middle">CARRY THE MOON</textPath>
      </text>

      <text class="remix-arc" letter-spacing="10">
        <textPath href="#remix-path" startOffset="50%" text-anchor="middle">REMIX</textPath>
      </text>
    </svg>

    <p class="credit">by OWEN TARRICK</p>
  </main>
</body>
</html>
```